Redesign two existing website pages and one new landing page for dental office

I need to redesign two webpages on my dental website, the Home page (http://velbridgedental.com) and the Dental Implant Services page (http://www.velbridgedental.com/dental-implant-services) and also create a landing page for the Dental Implant Services page.

Please use the same color scheme, slogans and subtitles for the redesign pages and create a reserved video spot on each page. The video spots should not be too big but not too small either and positioned in a central key location on each of the pages. The final redesigned pages should communicate leadership, confidence and trust.

The new landing page for the Dental implant Services page must not have any hyperlinks on the page and must entice the viewer to give name and email before downloading a "Free" eBook called "Is a Fuller Smile Worth the Wait?" Any added photo images to this new page must be smiling.
Updates

Project Deadline Extended Reason: I got feedback that my project was not long enough so I'm extending it by 5 days. Added Thursday, April 16, 2015

Target Market(s)

People who are middle-age to seniors.

Industry/Entity Type

Dental

Coding

Coded - Design and coding required

Number of Pages Required

3 page

Requirements
Must have
• Compatible with existing website colors and theme.

```html
<!DOCTYPE html>
<html lang="en">
<head>
<meta charset="utf-8">
<title>Velbridge Dental Care</title>
<link href="https://fonts.googleapis.com/css2?family=Raleway:wght@400;500;600;700&display=swap" rel="stylesheet">
<style>
:root{
  --green:#3d5c53;
  --green-dark:#2f4a42;
  --sage:#8fb0a3;
  --sage-btn:#7fa396;
  --light:#f2f2f2;
  --ink:#222;
  --muted:#444;
  --white:#fff;
}
*{margin:0;padding:0;box-sizing:border-box}
html,body{width:692px;height:1200px;overflow:hidden;background:var(--white)}
body{font-family:Arial,Helvetica,sans-serif;color:var(--ink);position:relative}
.abs{position:absolute}
.head{font-family:'Raleway',sans-serif}
/* header */
.site-header{top:0;left:0;width:692px;height:66px;background:var(--white)}
.brand{left:63px;top:20px;font-family:'Raleway',sans-serif;font-size:21px;font-weight:500;color:var(--green);display:flex;align-items:center;gap:6px}
.brand .mark{width:9px;height:9px;border-radius:50%;background:var(--green)}
.quick{top:21px;display:flex;align-items:center;gap:6px;font-size:8px;line-height:12px;color:var(--ink)}
.quick svg{width:24px;height:24px}
/* nav */
.main-nav{top:66px;left:0;width:692px;height:30px;background:var(--green)}
.main-nav a{position:absolute;top:0;height:30px;line-height:30px;color:var(--white);font-size:8.5px;text-decoration:none;letter-spacing:.2px}
.main-nav a.active{background:#1c1c1c;padding:0 12px;height:20px;line-height:20px;top:5px}
/* hero */
.hero{top:96px;left:0;width:692px;height:292px;background:linear-gradient(90deg,#d9dcd9 0%,#e8e4e0 40%,#dcc9bd 65%,#c9b2a4 100%)}
.hero-circle{top:38px;width:66px;height:66px;border-radius:50%;border:3px solid var(--white);box-shadow:0 1px 4px rgba(0,0,0,.3)}
.hero h1{left:58px;top:116px;font-family:'Raleway',sans-serif;font-size:21px;font-weight:600;line-height:24px;color:var(--white);text-shadow:0 1px 3px rgba(0,0,0,.45)}
.hero h1 span{color:var(--green);text-shadow:0 1px 2px rgba(255,255,255,.6)}
.hero p{left:58px;top:172px;width:310px;font-family:'Raleway',sans-serif;font-size:11px;line-height:18px;color:var(--white);text-shadow:0 1px 3px rgba(0,0,0,.45)}
.btn-hero{left:58px;top:224px;width:98px;height:29px;border-radius:5px;background:var(--green);color:var(--white);font-family:'Raleway',sans-serif;font-size:11px;line-height:29px;text-align:center;box-shadow:0 2px 3px rgba(0,0,0,.3)}
/* services */
.service{top:388px;height:245px;width:346px}
.service.hygiene{left:0;background:var(--light)}
.service.emergency{left:346px;width:346px;background:var(--green);color:var(--white)}
.service h2{position:absolute;left:0;top:13px;font-family:'Raleway',sans-serif;font-size:18px;font-weight:600}
.service h3{position:absolute;left:0;top:38px;font-family:'Raleway',sans-serif;font-size:13px;font-weight:400}
.service .photo{position:absolute;top:61px;width:256px;height:102px}
.service p{position:absolute;top:170px;width:260px;font-size:7.8px;line-height:13px}
.service .btn{position:absolute;top:206px;width:61px;height:24px;line-height:24px;font-size:8.5px;text-align:center;color:var(--white)}
/* features */
.feature{top:666px;width:140px;text-align:center}
.feature .icon{width:48px;height:48px;border-radius:50%;background:var(--green);margin:0 auto;display:flex;align-items:center;justify-content:center}
.feature h4{margin-top:19px;font-family:'Raleway',sans-serif;font-size:11px;font-weight:600;color:var(--ink)}
.feature ul{list-style:none;margin-top:9px;font-size:7.5px;line-height:14px;color:var(--muted)}
/* banner */
.banner{top:820px;left:0;width:692px;height:96px;background:var(--sage);text-align:center}
.banner h2{margin-top:12px;font-family:'Raleway',sans-serif;font-size:17px;font-weight:600;color:var(--white)}
.banner .btn{position:absolute;left:274px;top:42px;width:144px;height:41px;border-radius:5px;background:var(--green);color:var(--white);font-family:'Raleway',sans-serif;font-size:11px;line-height:14px;padding-top:7px;box-shadow:0 2px 3px rgba(0,0,0,.25)}
/* lower columns */
.col h3{font-family:'Raleway',sans-serif;font-size:14px;font-weight:600;color:var(--green)}
.col p{font-size:7.5px;line-height:10.5px;color:var(--muted)}
.posts{list-style:none;margin-top:8px;font-size:7.5px;line-height:16.2px;color:var(--muted)}
.posts li::before{content:"";display:inline-block;width:4px;height:4px;border-radius:50%;background:var(--muted);margin-right:6px;vertical-align:1px}
.about-doc{font-size:7.5px;color:var(--green);text-decoration:underline}
/* footer */
.site-footer{top:1099px;left:0;width:692px;height:101px;background:var(--green);color:var(--white)}
.social{left:63px;top:16px;display:flex;gap:3px}
.social span{width:18px;height:18px;background:#a7bbb3;border-radius:2px}
.foot-links{left:63px;top:42px;font-size:7.8px;line-height:14px}
.phone{left:472px;top:18px;display:flex;align-items:center;gap:8px;font-family:'Raleway',sans-serif;font-size:16px}
.foot-brand{left:472px;top:58px;font-family:'Raleway',sans-serif;font-size:18px;font-weight:500;color:#c9d6d1;display:flex;align-items:center;gap:6px}
.foot-brand .mark{width:8px;height:8px;border-radius:50%;background:#c9d6d1}
</style>
</head>
<body>

<header class="site-header abs">
  <div class="brand abs"><span class="mark"></span>Velbridge Dental Care</div>
  <div class="quick abs" style="left:348px">
    <svg viewBox="0 0 24 24" fill="none" stroke="#333" stroke-width="1.4"><rect x="3" y="3" width="9" height="17" rx="1.5"/><rect x="11" y="8" width="8" height="14" rx="1.5"/></svg>
    <span>Get Dr. Varden's<br>Mobile App</span>
  </div>
  <div class="quick abs" style="left:450px">
    <svg viewBox="0 0 24 24" fill="none" stroke="#333" stroke-width="1.4"><rect x="2" y="3" width="15" height="15" rx="1"/><path d="M5 7h9M5 10h6"/><circle cx="16" cy="16" r="6" fill="#fff"/><path d="M16 13v3h2"/></svg>
    <span>Request an<br>Appointment</span>
  </div>
  <div class="quick abs" style="left:549px">
    <svg viewBox="0 0 24 24" fill="none" stroke="#333" stroke-width="1.4"><path d="M4 2h11l4 4v16H4z"/><path d="M7 8h9M7 11h9M7 14h9M7 17h6"/></svg>
    <span>New Patient<br>Online Forms</span>
  </div>
</header>

<nav class="main-nav abs">
  <a class="active" style="left:66px">HOME</a>
  <a style="left:151px">ABOUT US</a>
  <a style="left:242px">DENTAL SERVICES</a>
  <a style="left:368px">BLOG</a>
  <a style="left:438px">CONTACT US</a>
  <a style="left:541px">TESTIMONIALS</a>
</nav>

<section class="hero abs" role="img" aria-label="Photo of a smiling young woman in a dental chair">
  <div class="hero-circle abs" style="left:59px;background:#e3c3ad" role="img" aria-label="Photo of a smiling child"></div>
  <div class="hero-circle abs" style="left:143px;background:#c9706a" role="img" aria-label="Close-up photo of healthy teeth"></div>
  <div class="hero-circle abs" style="left:228px;background:#b6bcc0" role="img" aria-label="Photo of dental instruments"></div>
  <h1 class="abs">Life-Changing <span>Family Dental</span><br>Care In Cedar Hollow</h1>
  <p class="abs">In this section you may find how our doctor treat with our patient and other lorem ipsum thing.</p>
  <div class="btn-hero abs">Appointment</div>
</section>

<section class="service hygiene abs">
  <h2 style="left:62px;color:var(--green)">Dental Hygiene Services</h2>
  <h3 style="left:63px;color:#444">Achieve Better Health With Prevention</h3>
  <div class="photo" style="left:66px;background:linear-gradient(90deg,#efe9e4,#d9b8a3 40%,#f4f1ee)" role="img" aria-label="Photo of a woman brushing her teeth"></div>
  <p style="left:67px">Maintain healthy teeth and gums with consistent dental exams and teeth cleanings by one of our professional dental hygienists.</p>
  <div class="btn" style="left:68px;background:var(--green)">Learn More</div>
</section>

<section class="service emergency abs">
  <h2 style="left:16px">Dental Emergency Services</h2>
  <h3 style="left:17px">Stop Pain From Tooth Trauma and Infection</h3>
  <div class="photo" style="left:20px;background:linear-gradient(90deg,#a9bccd,#dfe6ec 45%,#d6ae8e)" role="img" aria-label="Photo of a dentist examining a patient's teeth"></div>
  <p style="left:21px">Maintain healthy teeth and gums with consistent dental exams and teeth cleanings by one of our professional dental hygienists.</p>
  <div class="btn" style="left:23px;background:var(--sage-btn)">Learn More</div>
</section>

<div class="feature abs" style="left:42px">
  <div class="icon"><svg width="20" height="20" viewBox="0 0 20 20" fill="#fff"><rect x="2" y="5" width="16" height="12" rx="2"/><rect x="7" y="2" width="6" height="4" rx="1" fill="none" stroke="#fff" stroke-width="1.5"/><path d="M9 8h2v2h2v2h-2v2H9v-2H7v-2h2z" fill="#3d5c53"/></svg></div>
  <h4>Beautiful Dentures</h4>
  <ul><li>What is a Denture?</li><li>Who Needs a Denture?</li><li>Just How Are Dentures Made?</li></ul>
</div>
<div class="feature abs" style="left:194px">
  <div class="icon"><svg width="22" height="18" viewBox="0 0 22 18" fill="#fff"><path d="M1 5h13v9H1zM14 8h4l3 3v3h-7z"/><circle cx="5" cy="15" r="2"/><circle cx="17" cy="15" r="2"/><path d="M6.5 7h2v2h2v2h-2v2h-2v-2h-2V9h2z" fill="#3d5c53"/></svg></div>
  <h4>Cosmetic Dentistry</h4>
  <ul><li>What is a Denture?</li><li>Who Needs a Denture?</li><li>Just How Are Dentures Made?</li></ul>
</div>
<div class="feature abs" style="left:355px">
  <div class="icon"><svg width="18" height="20" viewBox="0 0 18 20" fill="#fff"><circle cx="9" cy="5" r="4"/><path d="M1 19c0-5 3-8 8-8s8 3 8 8z"/><circle cx="9" cy="16" r="2" fill="#3d5c53"/></svg></div>
  <h4>Dental Implant Services</h4>
  <ul><li>What is a Denture?</li><li>Who Needs a Denture?</li><li>Just How Are Dentures Made?</li></ul>
</div>
<div class="feature abs" style="left:514px">
  <div class="icon"><svg width="18" height="20" viewBox="0 0 18 20" fill="none" stroke="#fff" stroke-width="1.8"><path d="M3 2v6a4 4 0 0 0 8 0V2"/><path d="M7 12v2a4 4 0 0 0 8 0v-2"/><circle cx="15" cy="10" r="2"/></svg></div>
  <h4>Sedation Dentistry</h4>
  <ul style="margin-top:11px"><li>Control Dental Fear</li><li>Dental Pain Management</li><li>Relaxed and Tranquil</li></ul>
</div>

<section class="banner abs">
  <h2>Comprehensive Family Dentistry in One Cedar Hollow Dental Office!</h2>
  <div class="btn">Schedule<br>An Appointment?</div>
</section>

<section class="col abs" style="left:68px;top:943px;width:172px">
  <h3>Don't Wait 'til it Hurts!</h3>
  <div style="margin-top:9px;width:168px;height:73px;background:linear-gradient(90deg,#8fb3c9,#e6eef2 50%,#b8cfdc)" role="img" aria-label="Photo of a dental team treating a patient"></div>
  <p style="margin-top:5px">Get acquanted today with comfortable dental care.Request an Appointment! We will contact you right away to schedule...</p>
</section>

<section class="col abs" style="left:272px;top:941px;width:180px">
  <h3>Recent Blog Posts</h3>
  <ul class="posts">
    <li>Conscious Sedation: A Way to Deal with</li>
    <li>Anxiety at the Dentist's Office</li>
    <li>Pediatric Dentists and Their Importance in</li>
    <li>Today's World</li>
    <li>Tooth Implant Facts</li>
    <li>Is Sedation Dentistry Cost Affordable?</li>
    <li>How to Prepare for Oral Surgery</li>
  </ul>
</section>

<section class="col abs" style="left:478px;top:943px;width:156px">
  <h3>Dr. Elliot Varden</h3>
  <div style="position:relative;margin-top:9px;width:155px;height:98px;background:linear-gradient(180deg,#2a2a2a 0,#5a3b2c 12%,#7a5340 60%,#222 88%)" role="img" aria-label="Video of the dentist introducing the practice">
    <svg style="position:absolute;left:66px;top:40px" width="22" height="15" viewBox="0 0 22 15"><rect width="22" height="15" rx="3" fill="#1a1a1a"/><path d="M9 4l5 3.5-5 3.5z" fill="#fff"/></svg>
  </div>
  <div style="text-align:right;margin-top:8px"><span class="about-doc">● About Doctor</span></div>
</section>

<footer class="site-footer abs">
  <div class="social abs"><span></span><span></span><span></span><span></span><span></span></div>
  <div class="foot-links abs">Home &nbsp;| &nbsp;About Us &nbsp;| &nbsp;Dental Services &nbsp;| &nbsp;Blog &nbsp;| &nbsp;Contact Us &nbsp;| &nbsp;Testimonials<br>©2014 Velbridge Dental Care, Larkspur Medical Plaza, 480 Orchard Road, Ste.<br>#12, Cedar Hollow, TX 70000</div>
  <div class="phone abs"><svg width="18" height="18" viewBox="0 0 18 18" fill="none" stroke="#fff" stroke-width="1.3"><circle cx="9" cy="9" r="8"/><path d="M6 5l2 2-1 1.5c.6 1.2 1.3 1.9 2.5 2.5L11 10l2 2-1.2 1.3C9 13 5 9 4.8 6.2z" fill="#fff" stroke="none"/></svg>(555) 014-2290</div>
  <div class="foot-brand abs"><span class="mark"></span>Velbridge Dental Care</div>
</footer>

</body>
</html>
```